Looking for a cool & simple business-card-design for digital agency

Hi!

We are a web agency that offers Reputation Management, Vextor & Seo Services and software development. We like cool things, we like innovative styles.

We have uploaded our logo.

Project Deadline Extended Reason: Client does not want any designs with the colorful logo. Please send us submissions ONLY with the blac and white logo. What the client would like to see:1) Back of the card: is a silver logo on a black background2) front of the card with all the data, please use white background and black logo thank you Added Friday, May 8, 2015

Industry/Entity Type

Software

```html
<!DOCTYPE html>
<html lang="en">
<head>
<meta charset="utf-8">
<title>Brightlane AG – Business Card</title>
<link href="https://fonts.googleapis.com/css2?family=Open+Sans:wght@400;600;700&display=swap" rel="stylesheet">
<style>
  :root {
    --backdrop: #8d8d8d;
    --card-white: #f4f4f2;
    --card-black: #121212;
    --ink: #1a1a1a;
    --ink-soft: #3a3a3a;
    --accent: #b3121f;
    --silver: #c9cbcf;
  }
  html, body {
    margin: 0;
    padding: 0;
    width: 1200px;
    height: 1200px;
    overflow: hidden;
    background: var(--backdrop);
    font-family: "Open Sans", Arial, sans-serif;
  }
  .canvas {
    position: relative;
    width: 1200px;
    height: 1200px;
  }
  .card {
    position: absolute;
    left: 180px;
    width: 840px;
    height: 480px;
    box-sizing: border-box;
    box-shadow: 0 6px 18px rgba(0,0,0,0.25);
  }

  /* Front: contact side */
  .card-front {
    top: 90px;
    background: var(--card-white);
    color: var(--ink);
  }
  .brand {
    position: absolute;
    top: 56px;
    right: 56px;
    text-align: right;
  }
  .brand-row {
    display: flex;
    align-items: center;
    justify-content: flex-end;
    gap: 14px;
  }
  .brand-mark {
    width: 30px;
    height: 30px;
    background: var(--ink);
  }
  .brand-name {
    font-weight: 700;
    font-size: 40px;
    line-height: 1;
    color: var(--ink);
    letter-spacing: 0.5px;
  }
  .brand-tagline {
    margin-top: 8px;
    font-size: 17px;
    letter-spacing: 7px;
    margin-right: -7px;
    color: var(--ink-soft);
    text-transform: uppercase;
  }
  .person {
    position: absolute;
    top: 192px;
    right: 56px;
    text-align: right;
  }
  .person-name {
    font-weight: 700;
    font-size: 26px;
    line-height: 1.3;
    text-transform: uppercase;
  }
  .person-title {
    font-size: 21px;
    line-height: 1.3;
    color: var(--ink-soft);
  }
  .contact {
    position: absolute;
    left: 52px;
    top: 110px;
    margin: 0;
    padding: 0;
    list-style: none;
    font-size: 22px;
    line-height: 1.2;
    color: var(--ink-soft);
  }
  .contact li {
    display: flex;
    align-items: flex-start;
    gap: 12px;
    margin-bottom: 10px;
  }
  .contact svg {
    flex: none;
    width: 22px;
    height: 22px;
    margin-top: 2px;
  }
  .contact .address { margin-bottom: 22px; }

  /* Back: brand side */
  .card-back {
    top: 630px;
    background: var(--card-black);
    color: var(--silver);
  }
  .back-brand {
    position: absolute;
    right: 70px;
    bottom: 90px;
  }
  .back-brand-row {
    display: flex;
    align-items: center;
    gap: 22px;
  }
  .back-brand-mark {
    width: 70px;
    height: 70px;
    border-radius: 50%;
    background: var(--silver);
  }
  .back-brand-name {
    font-weight: 700;
    font-size: 72px;
    line-height: 1;
    color: var(--silver);
  }
  .back-brand-tagline {
    margin-top: 12px;
    padding-left: 92px;
    font-size: 26px;
    letter-spacing: 10px;
    text-transform: uppercase;
    color: var(--silver);
  }
</style>
</head>
<body>
<main class="canvas">

  <section class="card card-front" aria-label="Card front">
    <div class="brand">
      <div class="brand-row">
        <span class="brand-mark"></span>
        <span class="brand-name">Brightlane AG</span>
      </div>
      <div class="brand-tagline">Digitale Strategien</div>
    </div>

    <div class="person">
      <div class="person-name">Your Full Name</div>
      <div class="person-title">Your title</div>
    </div>

    <ul class="contact">
      <li class="address">
        <svg viewBox="0 0 22 22" aria-hidden="true"><circle cx="11" cy="11" r="11" fill="var(--accent)"/><path d="M11 5a4 4 0 0 0-4 4c0 3 4 8 4 8s4-5 4-8a4 4 0 0 0-4-4z" fill="#fff"/><circle cx="11" cy="9" r="1.5" fill="var(--accent)"/></svg>
        <span>Your company address line 1<br>City zipcode line 2</span>
      </li>
      <li>
        <svg viewBox="0 0 22 22" aria-hidden="true"><circle cx="11" cy="11" r="11" fill="var(--accent)"/><path d="M7 6l2.5-.5 1.2 2.8-1.5 1a7 7 0 0 0 3.5 3.5l1-1.5 2.8 1.2L16 15c-5 .5-9.5-4-9-9z" fill="#fff"/></svg>
        <span>012-345-6789</span>
      </li>
      <li>
        <svg viewBox="0 0 22 22" aria-hidden="true"><circle cx="11" cy="11" r="11" fill="var(--accent)"/><rect x="8" y="5" width="6" height="12" rx="1.2" fill="#fff"/><circle cx="11" cy="15" r=".9" fill="var(--accent)"/></svg>
        <span>012-345-6789</span>
      </li>
      <li>
        <svg viewBox="0 0 22 22" aria-hidden="true"><circle cx="11" cy="11" r="11" fill="var(--accent)"/><rect x="5.5" y="7" width="11" height="8" fill="#fff"/><path d="M5.5 7l5.5 4.5L16.5 7" fill="none" stroke="var(--accent)" stroke-width="1.2"/></svg>
        <span>your email adrress</span>
      </li>
      <li>
        <svg viewBox="0 0 22 22" aria-hidden="true"><circle cx="11" cy="11" r="11" fill="var(--accent)"/><circle cx="11" cy="11" r="5.5" fill="none" stroke="#fff" stroke-width="1.3"/><ellipse cx="11" cy="11" rx="2.4" ry="5.5" fill="none" stroke="#fff" stroke-width="1.1"/><path d="M5.5 11h11" stroke="#fff" stroke-width="1.1"/></svg>
        <span>www.yourdomain.com</span>
      </li>
    </ul>
  </section>

  <section class="card card-back" aria-label="Card back">
    <div class="back-brand">
      <div class="back-brand-row">
        <span class="back-brand-mark"></span>
        <span class="back-brand-name">Brightlane AG</span>
      </div>
      <div class="back-brand-tagline">Digitale Strategien</div>
    </div>
  </section>

</main>
</body>
</html>
```